Hollow Thicket, a 3d voxel survival video game needs a card for gaming conventions

I am the lead developer for Hollow Thicket http://www.HollowThicket.example and need a business card to hand out at an indie gaming convention
The card would need to include the game name, website url, my name, position (Lead Developer), e-mail and phone number
The game is a 3d, voxel (with smooth terrain) based survival game with guns and wildlife. The main icon of the game would likely be a grizzly bear but I am willing to accept other designs too.
Attached is a media kit for the game with some images you can use but don't have to its just what little art I can provide. Anything on the website or from the video game can also be used. unrelated art can also be used.
Target Market(s)
Indie Developers/publishers at conferences
Industry/Entity Type
Games
Contact Information for Business Card
Name: Corin Waldrick
Position: Lead Developer
E-mail: Pale_Kettle@mailbox.example
Phone number: 555-372-1186

```html
<!DOCTYPE html>
<html lang="en">
<head>
<meta charset="utf-8">
<title>Hollow Thicket — Business Card</title>
<link href="https://fonts.googleapis.com/css2?family=Rubik:wght@500;700&family=Roboto:wght@400&display=swap" rel="stylesheet">
<style>
  :root {
    --backdrop: #d6d6d6;
    --card-dark: #1d1d1e;
    --card-light-top: #ecebe6;
    --card-light-bottom: #cbc8bc;
    --fur-dark: #5a3a22;
    --fur-light: #9a6c47;
    --brand-red: #a81c1c;
    --brand-olive: #8e8a70;
    --wordmark: #b2352b;
    --ink: #1f1f1f;
    --ink-soft: #2e2e2e;
  }
  * { margin: 0; padding: 0; box-sizing: border-box; }
  html, body { width: 1200px; height: 1200px; overflow: hidden; }
  body { background: var(--backdrop); position: relative; font-family: "Roboto", sans-serif; }

  .card { position: absolute; left: 238px; width: 722px; height: 422px; overflow: hidden; }

  /* Front */
  .card--front { top: 118px; background: var(--card-dark); }
  .front__artwork {
    position: absolute; left: 214px; top: 72px; width: 190px; height: 168px;
    background: radial-gradient(closest-side ellipse at 50% 50%, var(--fur-light), var(--fur-dark) 65%, rgba(29,29,30,0) 100%);
  }
  .front__wordmark {
    position: absolute; left: 0; right: 0; top: 240px; text-align: center;
    font-family: "Rubik", sans-serif; font-weight: 700; font-size: 58px; line-height: 1;
    color: var(--wordmark); letter-spacing: 2px; text-transform: uppercase;
  }

  /* Back */
  .card--back { top: 644px; background: radial-gradient(ellipse at 60% 35%, var(--card-light-top), var(--card-light-bottom) 95%); }
  .back__artwork {
    position: absolute; left: 0; top: 38px; width: 318px; height: 362px;
    background: radial-gradient(closest-side ellipse at 50% 50%, var(--fur-light), var(--fur-dark) 62%, rgba(203,200,188,0) 100%);
  }
  .back__wordmark {
    position: absolute; right: 64px; top: 20px; width: 300px; text-align: right;
    font-family: "Rubik", sans-serif; font-weight: 700; font-size: 50px; line-height: 1.04;
    color: var(--wordmark); text-transform: uppercase;
  }
  .person { position: absolute; right: 58px; top: 190px; text-align: right; }
  .person__name { font-family: "Rubik", sans-serif; font-weight: 500; font-size: 24px; color: var(--ink); }
  .person__role { font-size: 16px; color: var(--ink-soft); margin-top: 8px; }

  .contacts { position: absolute; right: 58px; top: 274px; list-style: none; }
  .contacts li {
    display: flex; justify-content: flex-end; align-items: center; gap: 14px;
    font-size: 17px; color: var(--ink-soft); height: 26px;
  }
  .contacts svg { width: 16px; height: 16px; fill: var(--ink-soft); }

  .band { position: absolute; bottom: 0; left: 0; width: 722px; height: 44px; }
</style>
</head>
<body>
  <section class="card card--front">
    <div class="front__artwork" role="img" aria-label="Roaring grizzly bear photograph"></div>
    <div class="front__wordmark">Hollow<br>Thicket</div>
  </section>

  <section class="card card--back">
    <div class="back__artwork" role="img" aria-label="Grizzly bear standing on a rock photograph"></div>
    <div class="back__wordmark">Hollow<br>Thicket</div>

    <div class="person">
      <div class="person__name">Corin Waldrick</div>
      <div class="person__role">Lead Developer</div>
    </div>

    <ul class="contacts">
      <li>555-372-1186
        <svg viewBox="0 0 16 16"><path d="M2 5c0-2 3-3 6-3s6 1 6 3v1h-3V5H5v1H2z M4 7h8l2 6H2z"/></svg>
      </li>
      <li>www.hollowthicket.example
        <svg viewBox="0 0 16 16"><path d="M8 1a7 7 0 1 0 0 14A7 7 0 0 0 8 1zm0 1.5c.8 0 1.8 1.6 2.1 4H5.9C6.2 4.1 7.2 2.5 8 2.5zM2.6 7.5h2.2c0 .4 0 .7 0 1H2.6a5.6 5.6 0 0 1 0-1zm.3 2h2.1c.1 1.3.5 2.5 1 3.3A5.5 5.5 0 0 1 2.9 9.5zm3 0h4.2c-.3 2.4-1.3 4-2.1 4s-1.8-1.6-2.1-4zm5.1 0h2.1a5.5 5.5 0 0 1-3.1 3.3c.5-.8.9-2 1-3.3zm2.4-1h-2.2v-1h2.2a5.6 5.6 0 0 1 0 1zM11 6.5c-.1-1.3-.5-2.5-1-3.3a5.5 5.5 0 0 1 3.1 3.3zm-6 0H2.9A5.5 5.5 0 0 1 6 3.2c-.5.8-.9 2-1 3.3z"/></svg>
      </li>
      <li>Pale_Kettle@mailbox.example
        <svg viewBox="0 0 16 16"><path d="M1 3h14v10H1zm1.5 1.3v.4L8 8.8l5.5-4.1v-.4zm0 2.2v5.2h11V6.5L8 10.6z"/></svg>
      </li>
    </ul>

    <svg class="band" viewBox="0 0 722 44" aria-hidden="true">
      <polygon points="390,0 722,0 722,44 370,44" fill="var(--brand-olive)"/>
      <polygon points="0,22 387,22 378,44 0,44" fill="var(--brand-red)"/>
    </svg>
  </section>
</body>
</html>
```